Poster for a Bicycle show/Expo

We need a poster for a Bicycle show/Expo and sustainable transport. Exhibitors will sell bikes, cycling clothing, accessories, etc. ...
This show is annual and the Poster is for the 2015 edition.

The style must be modern, dynamic, bright colors.

Your concept must be compatible in a landscape format. (We will ourselves adaptations of different formats.)
Width: 210 mm
Height: 297 mm
It's necessary for us to have the source file (vector) for make, later, the different format (flyers, website, ...)

Content of the Poster:
- 1 big picture (no clip art)
- Big title: « Foire du Rayon » (« Salon » or « Salon du » can be small and « Vélo » big.)
- Subtitle: « et de la mobilité douce »
- Date: « 8, 9 et 10 mai 2015 » or « 8-10 mai 2015 »
- Place: « Halle TRV - Gare de Lunel »
- Text line 1: « www.foire-du-rayon.ch - Entrée gratuite »
- Text line 2« Piste d’essais - Restauration sur place »
- Text line 3: « Ve 8 mai de 17h à 21h - Sa 9 mai de 10h à 20h - Di 10 mai de 10h à 18h »
- Please, leave a zone in the poster for sponsors logos
(The predominant information (most visible) are: « Foire du Rayon » and « 8, 9 et 10 mai 2015 or 8-10 mai 2015 »)

Content of the big picture:
- from a cheap stock, like PixKiosk.com
- a bicycle in action or a detail of a bicycle (or a accessory) (no race bike)
- a modern picture with bright colors.
- if a person is on the picture, we prefer a men
- not an aerial view with cyclists in a landscape.

Some examples of poster of shows - with typo-title worked

http://www.expobassinlutece.com/Temp/IMG/F_a9b3c2d4e5f60718293a4b5c6d7e8f9012345678901_200_296.png

http://qx4m.tornafoire.fr/Data/pvtorn_mer/block/F_7cc1bb9396aef1d5e69283647561f0076457c357c5ea6.pdf
(page 2 of this PDF)

http://salons.rivol-evenements.fr/images/rivol-evenements/foires-salons/phototheque/salon-auto-bourlac/salon-auto-bourlac2012-affiche.jpg

http://www.tirovel.net/blog/wp-content/uploads/2007/03/affiche-salon-du-livre.jpg

http://www.quaimarin-gens.com/wp-content/affiche-cannes-2007.jpg
Updates

Hello,

For information, for your next versions, please, add the text "Piste d'essais".

- Text line 1: « www.foire-du-rayon.ch - Entrée gratuite »
- Text line 2: « Piste d’essais - Restauration sur place »
- Text line 3: « Ve 8 mai de 17h à 21h - Sa 9 mai de 10h à 20h - Di 10 mai de 10h à 18h »

Thanks,
Rodolphe

```html
<!DOCTYPE html>
<html lang="fr">
<head>
<meta charset="utf-8">
<title>Foire du Rayon et de la mobilité douce 2015</title>
<link href="https://fonts.googleapis.com/css2?family=Nunito+Sans:wght@400;600&display=swap" rel="stylesheet">
<style>
  :root {
    --lime: #a6c93a;
    --magenta: #ad3f8a;
    --orange: #f29a1f;
    --white: #ffffff;
    --photo-dark: #5f6062;
    --photo-mid: #9d9ea0;
    --photo-light: #cfd0d1;
  }
  html, body {
    margin: 0;
    padding: 0;
    overflow: hidden;
    background: #ffffff;
  }
  .poster {
    position: relative;
    width: 849px;
    height: 1200px;
    overflow: hidden;
    font-family: "Nunito Sans", "Avenir Next", sans-serif;
  }
  .hero-photo {
    position: absolute;
    inset: 0;
    background:
      radial-gradient(ellipse 30% 22% at 45% 45%, var(--photo-light), transparent 70%),
      radial-gradient(ellipse 35% 40% at 88% 70%, var(--photo-dark), transparent 75%),
      radial-gradient(ellipse 30% 30% at 10% 20%, var(--photo-dark), transparent 75%),
      linear-gradient(165deg, var(--photo-mid) 0%, var(--photo-light) 50%, var(--photo-mid) 100%);
  }
  .title {
    position: absolute;
    left: 98px;
    top: 338px;
    margin: 0;
    color: var(--lime);
    font-weight: 600;
    line-height: 0.86;
    letter-spacing: -3px;
  }
  .title span { display: block; }
  .title-small { font-size: 160px; }
  .title-big { font-size: 230px; letter-spacing: -7px; line-height: 0.8; }
  .tag {
    position: absolute;
    left: 105px;
    color: var(--white);
    box-sizing: border-box;
    white-space: nowrap;
  }
  .tag-subtitle {
    top: 849px;
    background: var(--magenta);
    font-size: 27px;
    line-height: 37px;
    padding: 0 14px;
  }
  .tag-when-where {
    top: 906px;
    background: var(--magenta);
    font-size: 22px;
    line-height: 45px;
    padding: 0 14px;
  }
  .tag-info, .tag-hours {
    background: var(--orange);
    font-size: 21px;
    line-height: 1.2;
    padding: 6px 14px 7px;
  }
  .tag-info { top: 962px; }
  .tag-hours { top: 1058px; }
  .tag p { margin: 0; }
</style>
</head>
<body>
<main class="poster">
  <div class="hero-photo" role="img" aria-label="Close-up black and white photograph of a bicycle wheel hub with spokes"></div>

  <h1 class="title">
    <span class="title-small">Foire</span>
    <span class="title-small">du</span>
    <span class="title-big">Rayon</span>
  </h1>

  <div class="tag tag-subtitle">et de la mobilité douce</div>
  <div class="tag tag-when-where">8, 9 et 10 mai 2015 | Halle TRV - Gare de Lunel</div>

  <div class="tag tag-info">
    <p>www.foire-du-rayon.ch</p>
    <p>Entrée gratuite</p>
    <p>Restauration sur place</p>
  </div>

  <div class="tag tag-hours">
    <p>Ve 8 mai de 17h à 21h</p>
    <p>Sa 9 mai de 10h à 20h</p>
    <p>Di 10 mai de 10h à 18h</p>
  </div>
</main>
</body>
</html>
```